Brenlow Estates Website and Logo Design

We need a new logo and website designed for 'Brenlow Estates Ltd', which is a well established Guernsey property holding company founded in 1934.

The company does not currently have a website. The new website should be similar in style and layout to https://www.quorvanhall.example/.

Target Market(s)

Industry, Media, Tenants

Industry/Entity Type

Property Management

Logo Text

BEL OR Brenlow Estates Ltd OR BE

Coding

Coded - Design and coding required

Number of Pages Required

4 page

Font styles to use
Other font styles liked:
• Helvetica

Requirements
Must have
• The logo laying over the picture (like https://www.quorvanhall.example/).
• Big pictures on homepage (like https://www.quorvanhall.example/)

```html
<!DOCTYPE html>
<html lang="en">
<head>
<meta charset="utf-8">
<title>Brenlow Estates – Property Management</title>
<link href="https://fonts.googleapis.com/css2?family=Lato:wght@400;700&display=swap" rel="stylesheet">
<style>
  :root {
    --night: #0a090d;
    --night-mid: #1e151c;
    --rock: #3b2631;
    --white: #ffffff;
    --rule: #9a9a9a;
    --lime: #9dc21b;
    --panel: #333333;
    --panel-text: #e6e6e6;
    --heading-dark: #333333;
    --page: #ffffff;
  }
  * { margin: 0; padding: 0; box-sizing: border-box; }
  html, body { width: 1200px; height: 1200px; overflow: hidden; background: var(--page); }
  body { position: relative; font-family: "Lato", Helvetica, Arial, sans-serif; }

  .hero { position: absolute; left: 0; top: 0; width: 1200px; height: 562px; overflow: hidden; }
  .hero-photo {
    position: absolute; inset: 0;
    background:
      radial-gradient(ellipse 140px 260px at 500px 470px, rgba(92,58,74,0.75), transparent 75%),
      radial-gradient(ellipse 130px 240px at 950px 460px, rgba(88,56,70,0.7), transparent 75%),
      radial-gradient(ellipse 260px 210px at 720px 190px, rgba(70,44,56,0.8), transparent 80%),
      radial-gradient(ellipse 220px 140px at 1170px 360px, rgba(110,96,36,0.5), transparent 75%),
      radial-gradient(ellipse 380px 200px at 360px 90px, rgba(60,56,66,0.55), transparent 80%),
      radial-gradient(ellipse 700px 120px at 300px 540px, rgba(40,28,36,0.9), transparent 80%),
      linear-gradient(180deg, #18161c 0%, var(--night) 50%, var(--night-mid) 100%);
  }
  .hero-content { position: absolute; left: 0; top: 0; width: 1200px; height: 562px; }
  .hero-title {
    position: absolute; top: 208px; left: 0; width: 1200px; text-align: center;
    color: var(--white); font-weight: 700; font-size: 35px; line-height: 44px; letter-spacing: -0.3px;
  }
  .hero-rule { position: absolute; top: 266px; left: 160px; width: 880px; height: 1px; background: var(--rule); }
  .hero-rule-accent { position: absolute; top: 265px; left: 536px; width: 128px; height: 3px; background: var(--lime); }
  .hero-text {
    position: absolute; top: 294px; left: 220px; width: 760px; text-align: center;
    color: var(--white); font-size: 12px; line-height: 18px;
  }

  .feature { position: absolute; top: 606px; width: 592px; height: 516px; }
  .feature-left { left: 0; }
  .feature-right { left: 608px; }
  .feature-photo { width: 592px; height: 374px; }
  .photo-city {
    background:
      radial-gradient(ellipse 60px 150px at 120px 280px, rgba(215,222,224,0.85), transparent 75%),
      radial-gradient(ellipse 140px 60px at 300px 60px, rgba(255,255,255,0.55), transparent 75%),
      radial-gradient(ellipse 160px 60px at 500px 55px, rgba(255,255,255,0.5), transparent 75%),
      radial-gradient(ellipse 200px 110px at 360px 320px, rgba(190,176,160,0.45), transparent 75%),
      linear-gradient(180deg, #1f8ea3 0%, #55b6c4 24%, #b6d6da 34%, #8ea8ae 40%, #6c8a90 55%, #4a5f65 78%, #38474c 100%);
  }
  .photo-meeting {
    background:
      radial-gradient(ellipse 110px 200px at 370px 220px, #1f2a44, rgba(31,42,68,0.6) 55%, transparent 80%),
      radial-gradient(ellipse 90px 170px at 110px 200px, rgba(150,150,150,0.75), transparent 80%),
      radial-gradient(ellipse 70px 200px at 575px 260px, rgba(30,38,60,0.85), transparent 80%),
      radial-gradient(ellipse 200px 60px at 300px 330px, rgba(255,255,255,0.9), transparent 80%),
      linear-gradient(180deg, #f1f3f5 0%, #e2e6ea 50%, #f4f5f6 100%);
  }
  .feature-panel { width: 592px; height: 142px; background: var(--panel); text-align: center; padding-top: 26px; }
  .feature-heading { color: var(--lime); font-weight: 700; font-size: 18px; line-height: 22px; }
  .feature-text { margin: 12px auto 0; width: 540px; color: var(--panel-text); font-size: 12px; line-height: 18px; }

  .gallery-heading {
    position: absolute; top: 1157px; left: 0; width: 1200px; text-align: center;
    color: var(--heading-dark); font-weight: 700; font-size: 38px; line-height: 46px;
  }
</style>
</head>
<body>
  <section class="hero">
    <div class="hero-photo" role="img" aria-label="Night sky full of stars behind a natural rock arch"></div>
    <div class="hero-content">
      <h1 class="hero-title">PROPERTY MANAGEMENT</h1>
      <div class="hero-rule"></div>
      <div class="hero-rule-accent"></div>
      <p class="hero-text">We provide complete rental Property Management and our services for luxury and affordable condos, apartments, penthouses, lofts, town-houses, houses and mansions. Our licensed Property Managers provide specialized services to suit the type of management appropriate to your real estate investment property and the options that best service you, our client.</p>
    </div>
  </section>

  <article class="feature feature-left">
    <div class="feature-photo photo-city" role="img" aria-label="Aerial view of a dense city skyline under a blue sky with clouds"></div>
    <div class="feature-panel">
      <h2 class="feature-heading">WHY GUERNSEY?</h2>
      <p class="feature-text">Lorem Ipsum is simply dummy text of the printing and typesetting industry. Lorem Ipsum has been the industry's standard dummy text ever since the 1500s, when an unknown printer took a galley of type and scrambled it to make a type specimen book</p>
    </div>
  </article>

  <article class="feature feature-right">
    <div class="feature-photo photo-meeting" role="img" aria-label="Business people meeting around a white table with documents and a tablet"></div>
    <div class="feature-panel">
      <h2 class="feature-heading">HOW WE CAN HELP YOU?</h2>
      <p class="feature-text">Lorem Ipsum is simply dummy text of the printing and typesetting industry. Lorem Ipsum has been the industry's standard dummy text ever since the 1500s, when an unknown printer took a galley of type and scrambled it to make a type specimen book</p>
    </div>
  </article>

  <h2 class="gallery-heading">GALLERY</h2>
</body>
</html>
```